A start up special flyer design!

Hi All - Have updated the attachment content - This is the info required for the designs.
I need a catchy flyer to send out to a few areas to advertise the start of my plumbing business!
The flyer will contain an offer for customers, which will need to have some key details on it. See attached. Feel free to fit these criteria into the flyer given your knowledge on design and messaging principles. Key thing to get across to customers is the discount and special offer, and that it is a start up offer.
I have a logo that needs to be on the flyer as well - let me know what format you require and I will send through to you.
The color scheme needs to be blue / grey / black / white.
Let me know if you have any questions.
I

```html
<!DOCTYPE html>
<html lang="en">
<head>
<meta charset="utf-8">
<title>Danny Flow Plumbing – Start-up Offer Flyer</title>
<link href="https://fonts.googleapis.com/css2?family=Oswald:wght@600;700&family=Roboto+Condensed:wght@500;700&family=Lato:ital,wght@0,400;1,400&display=swap" rel="stylesheet">
<style>
  :root {
    --blue: #1f56a8;
    --blue-deep: #173f80;
    --blue-bright: #2c6cc4;
    --charcoal: #3d3d3f;
    --grey: #6b6d70;
    --silver: #d9dbde;
    --white: #ffffff;
    --ink: #1b1b1d;
    --page: #e9eaec;
  }
  * { margin: 0; padding: 0; box-sizing: border-box; }
  html, body { width: 1200px; height: 960px; overflow: hidden; background: var(--page); }

  .flyer {
    position: absolute; left: 243px; top: 19px;
    width: 650px; height: 838px;
    transform: scale(1.1); transform-origin: 0 0;
    background: var(--white); overflow: hidden;
    box-shadow: 0 4px 18px rgba(0,0,0,.18);
  }
  .shapes { position: absolute; inset: 0; }

  .hero-photo {
    position: absolute; left: 0; top: 0; width: 650px; height: 337px;
    background: linear-gradient(120deg, #d8dde3 0%, #9aa3ad 40%, #4d5a6c 65%, #3f6ab0 100%);
    clip-path: polygon(258px 0, 650px 0, 650px 337px, 250px 337px, 312px 170px);
  }

  .headline {
    position: absolute; left: 25px; top: 38px;
    font: 700 35px/38px "Oswald", sans-serif; color: var(--white);
    text-transform: uppercase; letter-spacing: .2px;
  }
  .business-name {
    position: absolute; left: 34px; top: 198px;
    font-family: "Roboto Condensed", sans-serif; font-weight: 700; color: var(--blue);
    text-transform: uppercase;
  }
  .business-name .first { display: block; font-size: 34px; line-height: 40px; letter-spacing: .5px; }
  .business-name .second { display: block; font-size: 50px; line-height: 54px; letter-spacing: 1px; }

  .gallery {
    position: absolute; left: 8px; top: 372px; width: 630px; height: 190px;
    background: linear-gradient(90deg, #6b6d70, #9a9ca0 50%, #6b6d70);
    padding: 11px 10px; display: flex; gap: 4px;
  }
  .gallery .shot { flex: 1; height: 167px; }
  .shot-1 { background: linear-gradient(135deg, #e4e8ec, #3f6fb0 60%, #2b4f86); }
  .shot-2 { background: linear-gradient(160deg, #cfd5dc, #8a97a6 45%, #3a63a3); }
  .shot-3 { background: linear-gradient(140deg, #eef0f2, #b7bec6 50%, #4a5566); }

  .offer-bars { position: absolute; left: 0; top: 577px; }
  .offer-bar {
    height: 26px; margin-bottom: 9px; padding-left: 40px;
    background: var(--charcoal); color: var(--white);
    font: 500 13px/26px "Roboto Condensed", sans-serif; letter-spacing: .2px;
    clip-path: polygon(0 0, 100% 0, calc(100% - 22px) 100%, 0 100%);
  }
  .offer-bar.wide { width: 407px; }
  .offer-bar.mid { width: 378px; }
  .offer-bar.short { width: 352px; padding-left: 26px; }
  .offer-bar .dot::before {
    content: ""; display: inline-block; width: 7px; height: 7px; border-radius: 50%;
    background: var(--white); margin-right: 8px; vertical-align: 1px;
  }
  .offer-bar .gap { margin-left: 12px; }

  .terms {
    position: absolute; left: 34px; top: 697px; list-style: none;
    font: italic 400 12px/15px "Lato", sans-serif; color: var(--ink);
  }
  .terms li::before {
    content: ""; display: inline-block; width: 8px; height: 8px; border-radius: 50%;
    background: var(--blue); margin-right: 10px; vertical-align: 0;
  }

  .discount-badge {
    position: absolute; left: 398px; top: 583px; width: 166px; height: 166px;
    border-radius: 50%;
    background: linear-gradient(160deg, #f4f4f5, #8e9196 55%, #e6e7e9);
    box-shadow: 0 2px 6px rgba(0,0,0,.35);
  }
  .discount-badge .core {
    position: absolute; inset: 11px; border-radius: 50%;
    background: radial-gradient(circle at 40% 35%, var(--blue-bright), var(--blue-deep));
    border: 3px solid var(--white);
    display: flex; flex-direction: column; align-items: center; justify-content: center;
    color: var(--white); font-family: "Oswald", sans-serif; text-transform: uppercase;
  }
  .discount-badge .amount { font-size: 40px; line-height: 42px; font-weight: 700; text-transform: none; }
  .discount-badge .label { font-size: 18px; line-height: 22px; font-weight: 600; transform: scaleX(.82); white-space: nowrap; }

  .contact-bar {
    position: absolute; left: 0; bottom: 0; width: 650px; height: 65px;
    background: var(--charcoal); color: var(--white);
    display: flex; align-items: center; justify-content: center; gap: 16px;
    font: 400 12px "Lato", sans-serif;
  }
</style>
</head>
<body>
<main class="flyer">
  <div class="hero-photo" role="img" aria-label="Photo of a smiling plumber fitting black drain pipes under a sink"></div>

  <svg class="shapes" width="650" height="838" viewBox="0 0 650 838" aria-hidden="true">
    <defs>
      <linearGradient id="blue-band" x1="0" y1="0" x2="1" y2="1">
        <stop offset="0" stop-color="#1d4f9c"/><stop offset="1" stop-color="#2a66bd"/>
      </linearGradient>
      <linearGradient id="silver-panel" x1="0" y1="0" x2="1" y2="0">
        <stop offset="0" stop-color="#ffffff"/><stop offset=".55" stop-color="#eceef0"/><stop offset="1" stop-color="#c9ccd0"/>
      </linearGradient>
      <linearGradient id="offer-panel" x1="0" y1="0" x2="1" y2="1">
        <stop offset="0" stop-color="#2a68c0"/><stop offset="1" stop-color="#1c4f9c"/>
      </linearGradient>
    </defs>
    <!-- headline band -->
    <polygon points="0,0 246,0 302,168 0,168" fill="url(#blue-band)"/>
    <!-- name panel -->
    <polygon points="0,168 304,168 240,337 0,337" fill="url(#silver-panel)"/>
    <!-- diagonal divider -->
    <polyline points="252,0 310,170 246,337" fill="none" stroke="#1f56a8" stroke-width="5"/>
    <rect x="0" y="337" width="238" height="5" fill="#1f56a8"/>
    <rect x="246" y="337" width="404" height="5" fill="#ffffff"/>
    <rect x="0" y="342" width="650" height="6" fill="#ffffff"/>
    <!-- lower offer panels -->
    <polygon points="600,349 650,349 650,770 388,770" fill="#3d3d3f"/>
    <polygon points="612,349 650,349 650,770 408,770" fill="url(#offer-panel)"/>
    <rect x="0" y="768" width="650" height="5" fill="#1f56a8"/>
  </svg>

  <h1 class="headline">All plumbing<br>draining and<br>gasfitting works</h1>

  <h2 class="business-name"><span class="first">Danny Flow</span><span class="second">Plumbing</span></h2>

  <div class="gallery">
    <div class="shot shot-1" role="img" aria-label="Photo of a plumber in a blue cap repairing pipes under a sink"></div>
    <div class="shot shot-2" role="img" aria-label="Photo of a plumber working on overhead pipes with a wrench"></div>
    <div class="shot shot-3" role="img" aria-label="Photo of a plumber kneeling beside a bathtub with his tool bag"></div>
  </div>

  <div class="offer-bars">
    <p class="offer-bar wide">Plus, a free hot water health check and replacement quote</p>
    <p class="offer-bar mid">No GST payable, saving you additional 10% on your bill</p>
    <p class="offer-bar short"><span class="dot">Quality work at a decent price</span><span class="dot gap">Local plumber</span></p>
  </div>

  <ul class="terms">
    <li>Offer valid between 15 August 2016 to 15 October 2016</li>
    <li>Valid until 30 September 2016.</li>
    <li>Quote valid for 12 months from the quote date.</li>
  </ul>

  <div class="discount-badge">
    <div class="core">
      <span class="amount">15% off</span>
      <span class="label">Your overall bill</span>
    </div>
  </div>

  <footer class="contact-bar">
    <span>Ph: 0400 123 456</span>
    <span>Email: danny@dannyflowplumbing.com</span>
    <span>Web: www.dannyflowplumbing.com</span>
  </footer>
</main>
</body>
</html>
```